Presentation and Communication Coaching Services Business needs updated interactive web site

I want to keep the color scheme, functionality, and pages of my current site, but with a newer/updated look. I need to improve security and simplify images, etc. (Please see current site http://brightwellvoicetutor.com ) This will need be functional on mobile devices, as well.

I'm attached to the scrolling client list and scrolling client feedback.

Industry/Entity Type

Professional Service

Font styles to use
Sans Serif

Colors
0356a4
f37122
33a6d7

Requirements
Must have
• scrolling client banner on home page, client comments slider, color scheme
• Please see current site: http://brightwellvoicetutor.com
Nice to have
• better action/appearance
Should not have
• I don't want it to look like all the other sites/templates

```html
<!DOCTYPE html>
<html lang="en">
<head>
<meta charset="utf-8">
<title>Brightwell Voice Tutor</title>
<link rel="stylesheet" href="https://fonts.googleapis.com/css2?family=Poppins:ital,wght@0,300;0,400;0,500;0,600;0,700;1,400&display=swap">
<style>
:root{
  --blue:#0356a4;
  --orange:#f37122;
  --sky:#33a6d7;
  --ink:#222831;
  --grey:#6b6f76;
  --mark:#7a7d82;
  --light:#f3f4f6;
  --white:#ffffff;
}
*{margin:0;padding:0;box-sizing:border-box}
html,body{width:1200px;height:4534px;overflow:hidden}
body{position:relative;font-family:'Poppins',sans-serif;color:var(--ink);background:var(--white)}
.abs{position:absolute}
.nav{left:0;top:0;width:1200px;height:80px;background:var(--blue);display:flex;align-items:center;justify-content:space-between;padding:0 96px}
.brand{color:var(--white);font-size:22px;font-weight:400}
.nav ul{list-style:none;display:flex;gap:26px}
.nav li{color:var(--white);font-size:13px;font-weight:500;text-transform:uppercase}
.nav li.active{color:var(--orange)}
.hero{left:0;top:80px;width:1200px;height:640px;background:radial-gradient(ellipse at 75% 40%,#5b4a3c 0%,#2a2420 45%,#121010 100%)}
.hero-copy{left:170px;top:265px;width:600px;color:var(--white)}
.eyebrow{color:var(--orange);font-size:14px;font-weight:500;text-transform:uppercase;letter-spacing:.4px}
.hero h1{font-size:46px;font-weight:300;line-height:1.1;margin-top:10px}
.hero-copy p{font-size:12px;line-height:1.6;margin-top:26px;width:460px}
.btns{display:flex;gap:22px;margin-top:28px}
.btn{display:inline-flex;align-items:center;justify-content:center;height:38px;padding:0 20px;font-size:12px;font-weight:600;text-transform:uppercase;color:var(--white);white-space:nowrap}
.btn-orange{background:var(--orange)}
.btn-blue{background:var(--blue)}
.arrow{top:390px;width:52px;height:52px;background:var(--blue);display:flex;align-items:center;justify-content:center}
.about h2,.section-title{color:var(--blue);font-weight:700;text-transform:uppercase}
.about h2{font-size:44px;letter-spacing:.5px}
.about p{font-size:16px;line-height:1.65;color:var(--grey);margin-top:24px}
.more{font-size:14px;font-weight:600;color:var(--ink);margin-top:34px;display:inline-block;border-bottom:2px solid var(--ink);padding-bottom:6px;width:90px}
.section-title{font-size:48px;text-align:center;width:1200px;left:0}
.section-sub{left:380px;width:440px;text-align:center;font-size:15px;line-height:1.5;color:var(--grey)}
.card{text-align:center;padding:0 50px}
.card h3{font-size:17px;font-weight:600;text-transform:uppercase;margin-top:30px}
.card p{font-size:15px;line-height:1.65;margin-top:26px}
.card .btn{margin-top:30px;height:44px;padding:0 22px}
.card-white{background:var(--white);color:var(--ink)}
.card-white p{color:var(--grey)}
.card-blue{background:var(--sky);color:var(--white)}
.card-orange{background:var(--orange);color:var(--white)}
.btn-white{background:var(--white);color:var(--ink)}
.btn-sky{background:var(--sky)}
.services{left:0;top:2570px;width:1200px;height:890px;background-color:var(--light);background-image:radial-gradient(#dcdee2 1px,transparent 1px);background-size:8px 8px}
.svc h4{font-size:17px;font-weight:600;color:var(--blue);text-transform:uppercase}
.svc p{font-size:14px;line-height:1.55;color:var(--grey);margin-top:6px}
.hub-name{left:500px;top:2935px;width:200px;text-align:center;font-size:30px;font-weight:300;line-height:1.15;color:var(--mark)}
.quote-card{left:345px;top:3680px;width:505px;height:225px;background:var(--white);box-shadow:0 6px 22px rgba(0,0,0,.12);padding:22px 28px}
.quote-card .who{font-size:13px;font-weight:600}
.quote-card .role{font-size:9px;color:var(--grey)}
.quote-card p{font-size:10.5px;line-height:1.55;color:var(--grey);font-style:italic;margin-top:14px}
.stars{color:var(--orange);font-size:11px;margin-top:6px}
.clients{left:155px;top:3998px;width:890px;height:104px;background:var(--white);box-shadow:0 4px 16px rgba(0,0,0,.1);display:flex;align-items:center;justify-content:space-around}
.client{font-size:32px;font-weight:600;color:var(--ink);display:flex;align-items:center;gap:10px}
.client i{display:inline-block;width:14px;height:14px;background:var(--ink)}
.offer{left:0;top:4050px;width:1200px;height:200px;background:var(--orange)}
.footer{left:0;top:4250px;width:1200px;height:284px;background:var(--blue);color:var(--white)}
.footer h5{font-size:13px;font-weight:600;text-transform:uppercase;letter-spacing:.4px}
.footer li{list-style:none;font-size:11px;line-height:2.1;opacity:.9}
</style>
</head>
<body>

<header class="abs nav">
  <div class="brand">brightwell voicetutor</div>
  <ul>
    <li class="active">Home</li><li>About Us</li><li>Services</li><li>Clients</li><li>Speaking Secrets</li><li>Contact</li>
  </ul>
</header>

<section class="abs hero" role="img" aria-label="Photo of a speaker on stage holding a microphone before a large audience"></section>
<div class="abs hero-copy">
  <div class="eyebrow">Welcome to Brightwell Voice Tutor</div>
  <h1>You're good at what you do.<br>How to let it show.</h1>
  <p>You've done your best to reach this professional level. It's time to develop what it takes to reach the next one.</p>
  <div class="btns">
    <span class="btn btn-orange">&#9656;&nbsp; Read More</span>
    <span class="btn btn-blue">&#9679;&nbsp; Client Login</span>
  </div>
</div>
<div class="abs arrow" style="left:0"><svg width="18" height="18" viewBox="0 0 18 18"><path d="M12 3 5 9l7 6" fill="none" stroke="#fff" stroke-width="2"/></svg></div>
<div class="abs arrow" style="left:1148px"><svg width="18" height="18" viewBox="0 0 18 18"><path d="M6 3l7 6-7 6" fill="none" stroke="#fff" stroke-width="2"/></svg></div>

<section class="about">
  <div class="abs" style="left:275px;top:865px;width:42px;height:42px;border:6px solid var(--orange)"></div>
  <div class="abs" style="left:78px;top:930px;width:228px;height:230px;background:linear-gradient(135deg,#1f3b4d,#6e8ea3)" role="img" aria-label="Photo of a stage microphone"></div>
  <div class="abs" style="left:340px;top:845px;width:228px;height:230px;background:linear-gradient(135deg,#4a3a32,#b38f7a)" role="img" aria-label="Portrait photo of the coach"></div>
  <div class="abs" style="left:428px;top:1102px;width:60px;height:60px;background:var(--sky)"></div>
  <div class="abs" style="left:205px;top:1180px;width:28px;height:28px;background:#8fcbe8"></div>
  <div class="abs" style="left:258px;top:1110px;width:142px;height:142px;border:7px solid var(--orange);background:linear-gradient(135deg,#5b6b7a,#c0a894)" role="img" aria-label="Photo of the coach speaking at an event"></div>
  <div class="abs" style="left:625px;top:870px;width:440px">
    <h2>About Helena</h2>
    <p>Helena Brightwell is an Executive Coach for public speaking and all areas of spoken communication.</p>
    <p style="margin-top:20px">Helena delivers highly effective communication work­shops and individual coaching…</p>
    <span class="more">Full Story&nbsp;›</span>
  </div>
</section>

<h2 class="abs section-title" style="top:1365px">Our Features</h2>
<p class="abs section-sub" style="top:1428px">Lorem ipsum dolor sit amet, consectetur adipisicing elit, sed do eiusmod tempor incididunt ut labore et dolore magna aliqua</p>

<div class="abs card card-white" style="left:180px;top:1570px;width:405px;height:468px;padding-top:58px">
  <svg width="60" height="60" viewBox="0 0 60 60"><circle cx="28" cy="32" r="20" fill="none" stroke="#222" stroke-width="2.5"/><circle cx="28" cy="32" r="12" fill="none" stroke="#222" stroke-width="2.5"/><circle cx="28" cy="32" r="4" fill="#222"/><path d="M28 32 50 10M44 10h6v6" fill="none" stroke="#222" stroke-width="2.5"/></svg>
  <h3>The Goal</h3>
  <p>Lorem ipsum dolor sit amet, consectetur adipisicing elit, sed doadiadipisicing elit, sed do pisicing elit, sed do</p>
  <span class="btn btn-orange">Read More</span>
</div>
<div class="abs card card-blue" style="left:615px;top:1568px;width:443px;height:470px;padding-top:58px">
  <svg width="80" height="66" viewBox="0 0 80 66"><path d="M4 62h72" stroke="#fff" stroke-width="2.5"/><rect x="10" y="42" width="10" height="20" fill="none" stroke="#fff" stroke-width="2.5"/><rect x="26" y="32" width="10" height="30" fill="none" stroke="#fff" stroke-width="2.5"/><rect x="42" y="22" width="10" height="40" fill="none" stroke="#fff" stroke-width="2.5"/><rect x="58" y="12" width="10" height="50" fill="none" stroke="#fff" stroke-width="2.5"/><path d="M8 30 40 8l24-4M58 2h7v7" fill="none" stroke="#fff" stroke-width="2.5"/></svg>
  <h3>The Challenge</h3>
  <p>Lorem ipsum dolor sit amet, consectetur adipisicing elit, sed do eiusmod tempor incididunt ut labore et dolore magna</p>
  <span class="btn btn-white">Read More</span>
</div>
<div class="abs card card-orange" style="left:140px;top:2038px;width:445px;height:470px;padding-top:45px">
  <svg width="84" height="80" viewBox="0 0 84 80"><rect x="30" y="6" width="48" height="40" fill="none" stroke="#fff" stroke-width="2.5"/><path d="M38 36l10-10 8 6 14-14" fill="none" stroke="#fff" stroke-width="2.5"/><circle cx="18" cy="22" r="8" fill="none" stroke="#fff" stroke-width="2.5"/><path d="M6 74V44q0-10 12-10h8l14 8" fill="none" stroke="#fff" stroke-width="2.5"/><path d="M30 74V52" stroke="#fff" stroke-width="2.5"/></svg>
  <h3>The Solution</h3>
  <p>Lorem ipsum dolor sit amet, consectetur adipisicing elit, sed do eiusmod tempor incididunt ut labore et dolore magna</p>
  <span class="btn btn-white">Read More</span>
</div>
<div class="abs card card-white" style="left:615px;top:2040px;width:443px;height:468px;padding-top:80px">
  <svg width="44" height="56" viewBox="0 0 44 56"><rect x="3" y="6" width="38" height="48" fill="none" stroke="#222" stroke-width="2.5"/><rect x="13" y="2" width="18" height="8" fill="#222"/><path d="M10 20h24M10 28h24M10 36h24M10 44h16" stroke="#222" stroke-width="2.5"/></svg>
  <h3>The Result</h3>
  <p>Lorem ipsum dolor sit amet, consectetur adipisicing elit, sed doadiadipisicing elit, sed do pisicing elit, sed do</p>
  <span class="btn btn-sky">Read More</span>
</div>

<section class="abs services"></section>
<h2 class="abs section-title" style="top:2605px">Our Services</h2>
<p class="abs section-sub" style="top:2668px">Lorem ipsum dolor sit amet, consectetur adipisicing elit, sed do eiusmod tempo</p>

<svg class="abs" style="left:340px;top:2760px" width="520" height="480" viewBox="0 0 520 480">
  <path d="M147 55 A150 150 0 1 0 378 55" fill="none" stroke="#8a8a8a" stroke-width="14"/>
  <g fill="#fff" stroke="#f37122" stroke-width="6">
    <circle cx="147" cy="55" r="15"/><circle cx="378" cy="55" r="15"/>
    <circle cx="138" cy="238" r="15"/><circle cx="388" cy="238" r="15"/>
    <circle cx="265" cy="312" r="15"/>
  </g>
  <g fill="#0356a4" stroke="#b9d4ee" stroke-width="5">
    <circle cx="55" cy="70" r="40"/><circle cx="470" cy="70" r="40"/>
    <circle cx="60" cy="285" r="40"/><circle cx="470" cy="285" r="40"/>
    <circle cx="265" cy="380" r="40"/>
  </g>
  <g fill="none" stroke="#fff" stroke-width="2.5">
    <rect x="38" y="56" width="34" height="24"/><path d="M46 86h18"/>
    <circle cx="470" cy="60" r="9"/><path d="M454 90q0-16 16-16t16 16"/>
    <rect x="44" y="272" width="32" height="24"/><path d="M50 282h20M50 288h14"/>
    <circle cx="470" cy="278" r="10"/><path d="M456 302q0-12 14-12t14 12"/>
    <path d="M265 362l5 11 12 1-9 8 3 12-11-6-11 6 3-12-9-8 12-1z"/>
  </g>
</svg>
<div class="abs hub-name">Brightwell<br>Voice Tutor</div>

<div class="abs svc" style="left:120px;top:2808px;width:235px"><h4>01. Coaching</h4><p>One-on-one, individual, and customized to your unique goals, obstacles, and challenges. In person, or via videoconference.</p></div>
<div class="abs svc" style="left:120px;top:3037px;width:235px"><h4>02. Custom<br>Workshops</h4><p>Unique, effective program design and facilitation to match the needs of executives, managers, or promising individuals of any level.</p></div>
<div class="abs svc" style="left:893px;top:2808px;width:220px"><h4>03. Accents</h4><p>Support for executives from outside the U.S. to increase intelligibility and diminish obstacles to successful communication in American English.</p></div>
<div class="abs svc" style="left:896px;top:3040px;width:215px"><h4>04. Keynote<br>Speeches</h4><p>Fresh ways of thinking about speaking and communication combined with practical tools for participants of your next conference or event.</p></div>
<div class="abs svc" style="left:500px;top:3205px;width:215px;text-align:center"><h4>05. Secret Tips</h4><p>Fresh ways of thinking about speaking and communication combined with practical tools for participants of your next conference or event.</p></div>

<h2 class="abs section-title" style="top:3525px">Testimonials</h2>
<p class="abs section-sub" style="top:3588px">Lorem ipsum dolor sit amet, consectetur adipisicing elit, sed do eiusmod tempo</p>

<div class="abs quote-card">
  <div style="display:flex;align-items:center;gap:10px">
    <div style="width:34px;height:34px;border-radius:50%;background:linear-gradient(135deg,#c9a089,#7c5a4a)" role="img" aria-label="Client portrait"></div>
    <div><div class="who">DANA HOLLOWAY</div><div class="role">EASTON, EA<br>Senior Human Resource Specialist, Talent and People Development</div></div>
  </div>
  <p>Helena is an exceptional professional and a pleasure to work with. Most importantly, she delivers excellent results! Her expertise goes beyond just the delivery of a speech, and covers the content, structure, and how ideas land with an audience. Her insight is clear, warm and direct. I highly recommend Helena as a speech consultant.</p>
  <div class="stars">★★★★★</div>
</div>
<svg class="abs" style="left:838px;top:3752px" width="30" height="80" viewBox="0 0 30 80"><circle cx="15" cy="15" r="12" fill="none" stroke="#bbb" stroke-width="1.5"/><path d="M15 21V9M10 14l5-5 5 5" fill="none" stroke="#bbb" stroke-width="1.5"/><circle cx="15" cy="55" r="12" fill="none" stroke="#444" stroke-width="1.5"/><path d="M15 49v12M10 56l5 5 5-5" fill="none" stroke="#444" stroke-width="1.5"/></svg>

<section class="abs offer">
  <div class="abs" style="left:148px;top:98px;color:#fff">
    <div style="font-size:22px">Register and receive FREE "7 Traps in Everyday Speaking"</div>
    <div style="font-size:12px;opacity:.9;margin-top:4px">Lorem Ipsum is simply dummy text of the printing and typesetting industry.</div>
  </div>
  <span class="abs btn btn-white" style="left:898px;top:104px;height:42px;padding:0 22px">Register Now</span>
</section>
<div class="abs clients">
  <span class="client">Northfield</span>
  <span class="client">Vantora</span>
  <span class="client"><i></i>Cresthill</span>
  <span class="client">Quillmark</span>
</div>

<footer class="abs footer">
  <div class="abs" style="left:155px;top:68px;width:270px">
    <div style="font-size:18px">Brightwell Voice Tutor</div>
    <div style="font-size:11px;line-height:1.6;opacity:.85;margin-top:8px">Aenean lacinia bibendum nulla sed consectetur. Aenean eu leo quam.</div>
    <div style="display:flex;gap:16px;margin-top:20px"><span style="width:12px;height:12px;border-radius:50%;background:#6f9bd0"></span><span style="width:12px;height:12px;border-radius:50%;background:#6f9bd0"></span><span style="width:12px;height:12px;border-radius:50%;background:#6f9bd0"></span></div>
  </div>
  <div class="abs" style="left:578px;top:60px"><h5>Support</h5><ul style="margin-top:8px"><li>Help Center</li><li>Get Started</li><li>Contact Us</li></ul></div>
  <div class="abs" style="left:730px;top:60px"><h5>About Us</h5><ul style="margin-top:8px"><li>About Us</li><li>Terms of Use</li><li>Privacy Policy</li></ul></div>
  <div class="abs" style="left:882px;top:60px"><h5>Quick Contact</h5><ul style="margin-top:8px"><li>Phone : 555-014-2290</li><li>Address : Easton, EA 20410</li><li>Mail : info@brightwellvoicetutor.com</li></ul></div>
  <div class="abs" style="left:155px;top:218px;width:890px;border-top:1px solid rgba(255,255,255,.25)"></div>
  <div class="abs" style="left:0;top:236px;width:1200px;text-align:center;font-size:11px;opacity:.9">© 2019 Reserved to Brightwell Voice Tutor</div>
</footer>

</body>
</html>
```